Hardcore nerd needs to stand out in a sea of dull Defence business cards

Wombarra Devices is a new Australian consulting engineering company that turns research and theory into practical systems. No evangelistic fluff, just mathematics and physics into electronic and optical circuits for consumer products, scientific research or Defence applications.

We already have a recognised logo (provided) which is often dark blue/black on a light background but we're open to other combinations. (Us engineers tend to have limited aesthetic imagination :)

Some of our recent products have included:
* Instrumentation for electrical testing,
* Radar jammers,
* GPS antenna design,
* Satellite tracking systems,
* High power lasers

We're open to both single and double-sided designs - happy to be convinced either way.

P.S. Another group is working on the web page, so - alas - our web site is currently of no use for images/ideas...

Target Market(s)

Engineering managers,
Scientists

Contact Information for Business Card

Dr Colin Harte
R&D Engineer

colin@wombarradevices.com.au
0427 563 710

PO Box XXX (to be confirmed)
Kelsby ACT 2917
Australia

Font styles to use
Serif
Sans Serif

Colors

Designer to choose colors to be used in the design.

Requirements
Must have
• My contact details!
• I've had many (great) "bold and plain" designs submitted already, so feel free to be artistically creative :)
• Happy to take advice re fonts/colours/printability etc.
Nice to have
• I'm not sure if "lists" are more at home on a CV than a business card, but representative services include:
• Applied electromagnetics
• RF and high speed electronics
• Signal and image processing
• Electro-optical and laser systems
• Concept-to-prototype design services
• If you're considering double sided cards, then often measuring/alignment grids/rulers feature on the back of similar cards.
• e.g. https://www.veltranoptics.example/newgrouppage9.cfm?objectgroup_id=4183
• https://www.veltranoptics.example/newgrouppage9.cfm?objectgroup_ID=4185
• ..or even a "Smith chart" (google will return lots)
• Generic images to represent a capability might work - googling images associated with keyword for each of these areas might help:
• - "passive radar", "phased array", "fdtd", "vircator"
• RF and high speed electronic design
• - "smith chart", "microstrip circuits", "dimensioned drawing", "electronic schematic"
• - "dft", "iir filter"
• - "optical cavity". "laser energy level diagram"
• Background/watermarked images outlines/wireframes/schematics would probably look OK.
Should not have
• If a list of projects/services is provided, it is important not to make the client feel that this is "all" the company can do. Engineering design is a creative discipline (like graphics :)
• Please, no stock "military" snaps like planes, missiles, etc!

```html
<!DOCTYPE html>
<html lang="en">
<head>
<meta charset="utf-8">
<title>Wombarra Devices – Business Card</title>
<link rel="stylesheet" href="https://fonts.googleapis.com/css2?family=Arimo:wght@700&family=Lato:wght@400;700&display=swap">
<style>
  :root {
    --navy: #0c2461;
    --navy-rule: #0a1f57;
    --paper: #f6f6f7;
    --paper-shade: #ebebed;
    --backdrop: #e4e4e6;
    --white: #ffffff;
    --divider: rgba(255, 255, 255, 0.45);
  }
  * { margin: 0; padding: 0; box-sizing: border-box; }
  html, body {
    width: 1200px;
    height: 900px;
    overflow: hidden;
    background: var(--backdrop);
  }
  .stage {
    width: 1200px;
    height: 900px;
    display: flex;
    align-items: center;
    justify-content: center;
  }
  .card {
    width: 900px;
    height: 558px;
    display: flex;
    flex-direction: column;
    background: var(--paper);
    box-shadow: 0 10px 30px rgba(0, 0, 0, 0.18);
    overflow: hidden;
  }
  .card-brand {
    height: 272px;
    background: linear-gradient(180deg, var(--white) 0%, var(--paper) 55%, var(--paper-shade) 100%);
    display: flex;
    align-items: center;
    justify-content: center;
    gap: 22px;
    padding-top: 10px;
  }
  .brand-mark {
    width: 64px;
    height: 64px;
    border-radius: 50%;
    background: var(--navy);
    flex: none;
  }
  .brand-name {
    font-family: "Lato", sans-serif;
    font-weight: 700;
    font-size: 46px;
    color: var(--navy);
    line-height: 1;
    white-space: nowrap;
  }
  .card-rule {
    height: 3px;
    background: var(--navy-rule);
  }
  .card-gap {
    height: 4px;
    background: var(--white);
  }
  .card-contact {
    flex: 1;
    background: var(--navy);
    color: var(--white);
    display: flex;
    flex-direction: column;
    align-items: center;
    text-align: center;
    padding-top: 30px;
    font-family: "Lato", sans-serif;
    font-size: 24px;
    line-height: 1.3;
  }
  .person-name {
    font-family: "Arimo", sans-serif;
    font-weight: 700;
    font-size: 32px;
    letter-spacing: 0.5px;
    line-height: 1;
  }
  .person-role {
    margin-top: 4px;
  }
  .divider {
    width: 296px;
    height: 1px;
    background: var(--divider);
    margin: 10px 0;
  }
  .contact-line { display: block; }
</style>
</head>
<body>
  <main class="stage">
    <article class="card">
      <header class="card-brand">
        <span class="brand-mark" aria-hidden="true"></span>
        <h1 class="brand-name">Wombarra Devices</h1>
      </header>
      <div class="card-rule"></div>
      <div class="card-gap"></div>
      <section class="card-contact">
        <h2 class="person-name">DR COLIN HARTE</h2>
        <p class="person-role">R&amp;D Engineer</p>
        <div class="divider"></div>
        <p class="contact-line">0427 563 710</p>
        <p class="contact-line">colin@wombarradevices.com.au</p>
        <div class="divider"></div>
        <p class="contact-line">PO Box XXX&nbsp; Kelsby ACT 2917, Australia</p>
      </section>
    </article>
  </main>
</body>
</html>
```